Maplecrest Disability - Social Security Disability Attorneys

Our company is expanding to attract clients nationwide for our social security disability practice. We have a logo, but I am looking for a creative and elegant letterhead that projects an image of being technologically advanced but still professional enough for the legal field. I am looking for the "wow factor" combined with this is still professional enough for a law practice.

Requesting letterhead and business card design
Updates

Had to update and change the logo. The previous logo had a typo. Please send updates with the new logo for consideration. The letterhead and business cards should be professional enough to be used for a law firm. Thanks.

Industry/Entity Type

Law Practice, Law Firm, Healthcare Industry, Government

Colors

Designer to choose colors to be used in the design.

Requirements
Nice to have
• **Please create a vertical design for the business card**

```html
<!DOCTYPE html>
<html lang="en">
<head>
<meta charset="utf-8">
<title>Maplecrest Disability – Business Card</title>
<link rel="stylesheet" href="https://fonts.googleapis.com/css2?family=Montserrat:wght@400;500;700&display=swap">
<style>
  :root {
    --backdrop: #e7e1d8;
    --card-top: #f7f5f2;
    --card-bottom: #eef3f8;
    --card-edge: #ffffff;
    --brand-blue: #3f4f86;
    --brand-orange: #e0731f;
    --ink: #1d1d1f;
  }
  * { box-sizing: border-box; margin: 0; padding: 0; }
  html, body { width: 1200px; height: 943px; overflow: hidden; }
  body {
    background: var(--backdrop);
    font-family: "Montserrat", sans-serif;
    color: var(--ink);
  }
  .business-card {
    position: absolute;
    left: 366px;
    top: 62px;
    width: 468px;
    height: 820px;
    border-radius: 30px;
    border: 2px solid var(--card-edge);
    background: linear-gradient(180deg, var(--card-top) 0%, #f3f1ee 45%, var(--card-bottom) 100%);
    box-shadow: 0 10px 30px rgba(60, 50, 40, 0.15);
    overflow: hidden;
    text-align: center;
  }
  .brand-mark {
    position: absolute;
    left: 50%;
    top: 140px;
    width: 26px;
    height: 26px;
    margin-left: -13px;
    border-radius: 50%;
    background: var(--brand-orange);
  }
  .brand-name {
    position: absolute;
    top: 192px;
    width: 100%;
    font-size: 25px;
    font-weight: 500;
    letter-spacing: 1.5px;
    text-transform: uppercase;
    color: var(--brand-blue);
  }
  .brand-tagline {
    position: absolute;
    top: 230px;
    width: 100%;
    font-size: 8.5px;
    font-weight: 500;
    letter-spacing: 2.6px;
    text-transform: uppercase;
    color: var(--brand-blue);
  }
  .holder-name {
    position: absolute;
    top: 318px;
    width: 100%;
    font-size: 27px;
    font-weight: 700;
    color: var(--brand-orange);
    text-transform: uppercase;
  }
  .holder-role {
    position: absolute;
    top: 355px;
    width: 100%;
    display: flex;
    align-items: center;
    justify-content: center;
    gap: 6px;
    font-size: 19px;
    font-weight: 400;
  }
  .holder-role::before,
  .holder-role::after {
    content: "";
    width: 62px;
    height: 2px;
    background: var(--brand-orange);
  }
  .office-address {
    position: absolute;
    top: 450px;
    width: 100%;
    font-size: 17px;
    line-height: 28px;
    font-weight: 400;
  }
  .contact-icons {
    position: absolute;
    top: 537px;
    width: 100%;
    display: flex;
    justify-content: center;
    gap: 44px;
  }
  .contact-icons svg { width: 30px; height: 30px; display: block; }
  .contact-list {
    position: absolute;
    top: 600px;
    width: 100%;
    list-style: none;
    font-size: 17px;
    line-height: 31px;
    font-weight: 400;
  }
  .card-wave {
    position: absolute;
    left: 0;
    bottom: 0;
    width: 100%;
    height: 58px;
    display: block;
  }
</style>
</head>
<body>
  <article class="business-card">
    <span class="brand-mark" aria-hidden="true"></span>
    <h1 class="brand-name">Maplecrest Disability</h1>
    <p class="brand-tagline">Social Security Disability Attorneys</p>

    <h2 class="holder-name">Daniel Whitcombe</h2>
    <p class="holder-role">Co-Founder</p>

    <p class="office-address">Suite 4, Level 12, Harbour Lane<br>Sydney NSW 2000</p>

    <div class="contact-icons" aria-hidden="true">
      <svg viewBox="0 0 30 30">
        <rect width="30" height="30" fill="var(--brand-orange)"/>
        <path d="M9 7.5c1-.8 2-.6 2.6.3l1.6 2.6c.5.8.3 1.6-.4 2.2l-1 .8c.9 2 2.5 3.7 4.6 4.7l.8-1c.6-.7 1.5-.9 2.2-.4l2.6 1.6c.9.6 1.1 1.7.3 2.6l-1.2 1.3c-1 1-2.6 1.2-4 .5-4.3-2-7.6-5.4-9.5-9.7-.6-1.4-.3-3 .8-4z" fill="#fff"/>
      </svg>
      <svg viewBox="0 0 30 30">
        <rect width="30" height="30" fill="var(--brand-orange)"/>
        <rect x="6" y="9" width="18" height="12" fill="none" stroke="#fff" stroke-width="1.8"/>
        <path d="M6 9l9 7 9-7M6 21l7-6M24 21l-7-6" fill="none" stroke="#fff" stroke-width="1.6"/>
      </svg>
      <svg viewBox="0 0 30 30">
        <rect width="30" height="30" fill="var(--brand-orange)"/>
        <circle cx="15" cy="15" r="8.5" fill="none" stroke="#fff" stroke-width="1.8"/>
        <ellipse cx="15" cy="15" rx="3.6" ry="8.5" fill="none" stroke="#fff" stroke-width="1.4"/>
        <path d="M6.5 15h17" stroke="#fff" stroke-width="1.4"/>
      </svg>
    </div>

    <ul class="contact-list">
      <li>555-014-2290</li>
      <li>Info@maplecrestdisability.com</li>
      <li>www.maplecrestdisability.com</li>
    </ul>

    <svg class="card-wave" viewBox="0 0 468 58" preserveAspectRatio="none" aria-hidden="true">
      <path d="M0 20 C90 46 170 40 270 26 C350 14 420 8 468 12 L468 58 L0 58 Z" fill="var(--brand-blue)"/>
      <path d="M0 6 C80 34 170 30 270 18 C350 8 420 2 468 6" fill="none" stroke="var(--brand-orange)" stroke-width="5"/>
    </svg>
  </article>
</body>
</html>
```